Professional & attention grabbing.

A business card design, front and back. I already have a logo I will attach, but I am open to something new as well.
Things to include:
Name:
Title:
Phone:
Email:
Wanting something that is professional but attention grabbing.
Also we do a lot of work using drones on natural gas pipelines (leading the future)if you want to include any of that. I'm open to ideas.
Target Market(s)
Natural gas transmission industry / greenhouse gas mitigation industry
Industry/Entity Type
Business
Colors
Designer to choose colors to be used in the design.
Look and feel
Each slider illustrates characteristics of the customer's brand and the style your logo design should communicate.

```html
<!DOCTYPE html>
<html lang="en">
<head>
<meta charset="utf-8">
<title>KV Field Inspections – Business Card</title>
<link href="https://fonts.googleapis.com/css2?family=Source+Sans+3:wght@400;600;700&display=swap" rel="stylesheet">
<style>
  :root {
    --backdrop: #b4b4b4;
    --card-white: #ffffff;
    --charcoal: #3a3a3c;
    --charcoal-light: #4a4a4d;
    --charcoal-deep: #333335;
    --brand-red: #c0202a;
    --ink: #1f1f1f;
  }
  html, body {
    margin: 0;
    padding: 0;
    overflow: hidden;
  }
  body {
    width: 1200px;
    height: 900px;
    background: var(--backdrop);
    position: relative;
    font-family: "Source Sans 3", sans-serif;
  }
  .card {
    position: absolute;
    top: 306px;
    width: 440px;
    height: 271px;
    overflow: hidden;
  }
  .card-front {
    left: 149px;
    background: var(--card-white);
  }
  .card-back {
    left: 608px;
    background: var(--charcoal);
    border-radius: 10px;
  }
  .front-band {
    position: absolute;
    left: 319px;
    top: 0;
    width: 121px;
    height: 100%;
    background: var(--charcoal);
  }
  .front-frame {
    position: absolute;
    left: 261px;
    top: 69px;
    width: 132px;
    height: 145px;
    background: var(--card-white);
  }
  .front-frame-core {
    position: absolute;
    left: 16px;
    top: 14px;
    width: 100px;
    height: 116px;
    background: var(--charcoal);
  }
  .brand-lockup {
    position: absolute;
    left: 23px;
    top: 38px;
    display: flex;
    align-items: center;
    gap: 8px;
  }
  .brand-square {
    width: 14px;
    height: 14px;
    background: var(--brand-red);
  }
  .brand-name {
    font-weight: 700;
    font-size: 17px;
    color: var(--charcoal);
    letter-spacing: 0.2px;
  }
  .holder {
    position: absolute;
    left: 23px;
    top: 163px;
  }
  .holder-name {
    margin: 0;
    font-weight: 600;
    font-size: 16px;
    line-height: 18px;
    color: var(--brand-red);
    text-transform: uppercase;
  }
  .holder-title {
    margin: 0;
    font-size: 13px;
    line-height: 15px;
    color: var(--ink);
  }
  .contacts {
    position: absolute;
    left: 24px;
    top: 212px;
    margin: 0;
    padding: 0;
    list-style: none;
    font-size: 13px;
    line-height: 17px;
    color: var(--ink);
  }
  .contacts li {
    display: flex;
    align-items: center;
    gap: 5px;
  }
  .contacts svg {
    width: 10px;
    height: 10px;
    fill: var(--brand-red);
  }
  .back-pattern {
    position: absolute;
    inset: 0;
    background:
      radial-gradient(ellipse at 20% 25%, var(--charcoal-light) 0%, transparent 55%),
      radial-gradient(ellipse at 80% 80%, var(--charcoal-light) 0%, transparent 50%),
      linear-gradient(135deg, var(--charcoal-light), var(--charcoal-deep));
  }
  .back-lockup {
    position: absolute;
    inset: 0;
    display: flex;
    align-items: center;
    justify-content: center;
    gap: 10px;
  }
  .back-lockup .brand-square {
    width: 18px;
    height: 18px;
  }
  .back-lockup .brand-name {
    color: var(--card-white);
    font-size: 22px;
  }
</style>
</head>
<body>
  <section class="card card-front" aria-label="Business card front">
    <div class="front-band"></div>
    <div class="front-frame"><div class="front-frame-core"></div></div>

    <div class="brand-lockup">
      <span class="brand-square"></span>
      <span class="brand-name">KV Field Inspections</span>
    </div>

    <div class="holder">
      <p class="holder-name">Daniel Harper</p>
      <p class="holder-title">Managing Director</p>
    </div>

    <ul class="contacts">
      <li>
        <svg viewBox="0 0 10 10" aria-hidden="true"><path d="M2 0.5 L3.6 2.6 L2.8 3.6 Q3.8 5.8 6.2 7.1 L7.3 6.3 L9.5 7.9 L8.4 9.5 Q4.5 9.3 1.6 5.9 Q0.3 4 0.5 1.6 Z"/></svg>
        <span>(044)987654321</span>
      </li>
      <li>
        <svg viewBox="0 0 10 10" aria-hidden="true"><path d="M0 2 H10 V8.5 H0 Z M0.6 2.4 L5 5.6 L9.4 2.4" stroke="#fff" stroke-width="0.8"/></svg>
        <span>hello@kvfield.com</span>
      </li>
    </ul>
  </section>

  <section class="card card-back" aria-label="Business card back">
    <div class="back-pattern" role="img" aria-label="Faint repeating tonal brand pattern covering the whole dark card"></div>
    <div class="back-lockup">
      <span class="brand-square"></span>
      <span class="brand-name">KV Field Inspections</span>
    </div>
  </section>
</body>
</html>
```